New, modern business card for growing audiology practice

We need a new business card for our audiology practice. Our logo and website have recently changed (more modern) and we want our business cards to reflect this change.
We conduct hearing tests, perform earwax removals, and fit & dispense hearing aids to our patients. We are a family owned practice in which the owner is the one who works directly with the patient. I have attached logos in various formats to use, as well as two ideas I found on this website; as well as a scanned copy of our current logo. Good luck!

Industry/Entity Type

Business

Contact Information for Business Card

Company name: Tolvera Hearing Center
Provider name: Peter Wolstenby, Au.D. F/NSB
Phone number: (440) 683-5127
Address: 837 W. Lindell Ave. Marlow Falls, OH 44097
email: tolverahearing@postvane.com
website: tolverahearing.com

Colors
000000
aaaaaa
dbdbdb
cacaca
9bcb3c
afd23c
cadf82
b1b1b1

Requirements
Must have
• My card must include information in the "details" section. In the attached images, I found a few that I liked and I would like to model after - "brisky bouncin'" and "Sound Method Center".
• Must be horizontal.
• Must include logos provided. I uploaded them in various file formats and various ways.
• Must match logo font, if possible, if not, please get as close as you can.
Nice to have
• I really like the idea of having a color on one side with just the logo and company name and the contact information and provider name on the other side. I also really like the idea of having the main color dominating on the logo/company side with accent of that same color on the contact side of the card.
Should not have
• Must not be vertical.

```html
<!DOCTYPE html>
<html lang="en">
<head>
<meta charset="utf-8">
<title>Tolvera Hearing Center – Business Card</title>
<link rel="stylesheet" href="https://fonts.googleapis.com/css2?family=Roboto:wght@400;500&family=Roboto+Condensed:wght@700&display=swap">
<style>
  :root {
    --page-bg: #e4e4e4;
    --card-white: #f2f2f2;
    --brand-green: #6f9e35;
    --ink-black: #000000;
    --text-grey: #4a4a4a;
    --text-white: #ffffff;
  }
  html, body {
    margin: 0;
    width: 1200px;
    height: 960px;
    overflow: hidden;
    background: var(--page-bg);
  }
  .card {
    position: absolute;
    width: 600px;
    height: 343px;
    overflow: hidden;
    font-family: "Roboto", Arial, sans-serif;
  }
  .card--front { left: 314px; top: 113px; background: var(--card-white); }
  .card--back  { left: 311px; top: 472px; background: var(--ink-black); }

  .front-swoosh { position: absolute; inset: 0; }

  .provider {
    position: absolute;
    right: 33px;
    top: 33px;
    text-align: right;
    color: var(--text-white);
  }
  .provider__name {
    font-family: "Roboto Condensed", "Arial Narrow", sans-serif;
    font-weight: 700;
    font-size: 21px;
    margin: 0;
  }
  .provider__credentials {
    font-weight: 500;
    font-size: 14px;
    margin: 4px 0 0;
    letter-spacing: 0.3px;
  }

  .brand {
    position: absolute;
    display: flex;
    align-items: center;
    white-space: nowrap;
  }
  .brand__dot {
    border-radius: 50%;
    background: var(--brand-green);
    flex: none;
  }
  .brand__name { font-family: "Roboto", Arial, sans-serif; font-weight: 400; text-transform: uppercase; }

  .card--front .brand { left: 34px; top: 169px; }
  .card--front .brand__dot { width: 16px; height: 16px; margin-right: 9px; }
  .card--front .brand__name { font-size: 17px; color: var(--ink-black); }

  .address {
    position: absolute;
    left: 34px;
    top: 215px;
    margin: 0;
    font-size: 14px;
    line-height: 19px;
    color: var(--text-grey);
    font-style: normal;
  }
  .contact {
    position: absolute;
    left: 34px;
    top: 262px;
    margin: 0;
    padding: 0;
    list-style: none;
    font-size: 14px;
    line-height: 19.5px;
    color: var(--text-grey);
  }
  .contact__item { display: flex; align-items: center; }
  .contact__icon { width: 13px; height: 13px; margin-right: 9px; fill: var(--brand-green); }

  .card--back .brand { left: 0; right: 0; top: 155px; justify-content: center; }
  .card--back .brand__dot { width: 30px; height: 30px; margin-right: 14px; }
  .card--back .brand__name { font-size: 28px; color: var(--text-white); }

  .back-web {
    position: absolute;
    left: 0; right: 0;
    top: 287px;
    text-align: center;
    font-size: 14px;
    letter-spacing: 3.5px;
    color: var(--text-white);
    margin: 0;
  }
  .back-web__domain { color: var(--brand-green); }
</style>
</head>
<body>

<section class="card card--front" aria-label="Card front">
  <svg class="front-swoosh" width="600" height="343" viewBox="0 0 600 343" aria-hidden="true">
    <path class="swoosh-band" d="M226,0 C390,60 522,165 552,262 C564,302 561,326 555,343 L600,343 L600,0 Z" fill="var(--ink-black)"/>
    <path class="swoosh-field" d="M226,0 C380,55 505,152 536,250 C549,292 536,325 506,343 L600,343 L600,0 Z" fill="var(--brand-green)" stroke="#ffffff" stroke-width="2"/>
  </svg>

  <div class="provider">
    <h1 class="provider__name">PETER WOLSTENBY</h1>
    <p class="provider__credentials">AU.D. F/NSB</p>
  </div>

  <div class="brand">
    <span class="brand__dot"></span>
    <span class="brand__name">Tolvera Hearing Center</span>
  </div>

  <address class="address">837 W. Lindell Ave.<br>Marlow Falls, OH 44097</address>

  <ul class="contact">
    <li class="contact__item">
      <svg class="contact__icon" viewBox="0 0 16 16" aria-hidden="true"><path d="M3.6 1 L6 1.4 7 5 5.4 6.4 C6.3 8.3 7.7 9.7 9.6 10.6 L11 9 14.6 10 15 12.4 13 15 C6.5 14.3 1.7 9.5 1 3 Z"/></svg>
      (440) 683-5127
    </li>
    <li class="contact__item">
      <svg class="contact__icon" viewBox="0 0 16 16" aria-hidden="true"><path d="M1 3 H15 V4 L8 8.5 1 4 Z M1 5.5 L8 10 15 5.5 V13 H1 Z"/></svg>
      tolverahearing@postvane.com
    </li>
    <li class="contact__item">
      <svg class="contact__icon" viewBox="0 0 16 16" aria-hidden="true"><circle cx="8" cy="8" r="7"/><path d="M4 5 C6 4 7 6 6 8 C5 10 7 11 8 13 M10 3 C11 5 12 6 13 7" stroke="#f2f2f2" stroke-width="1.3" fill="none"/></svg>
      tolverahearing.com
    </li>
  </ul>
</section>

<section class="card card--back" aria-label="Card back">
  <div class="brand">
    <span class="brand__dot"></span>
    <span class="brand__name">Tolvera Hearing Center</span>
  </div>
  <p class="back-web">www.<span class="back-web__domain">tolverahearing</span>.com</p>
</section>

</body>
</html>
```